Cover für den Roman Hanna betritt die Leinwand
Zielgruppe
Autorin einer belletristischen Erzählung über die Kunst der Moderne. Das Buch richtet sich an Leser die sich für Moderne Kunst interessieren.
Aufgabenstellung
Gesucht wird ein sehr zeitgemäßes und auffallendes Design, auch gerne mit einer starken Hintergrundfarbe. Der Leser soll auf den ersten Blick erkennen können, dass es hier um Kunst geht (Odo Marquet, Drosanow, Veluzzi Ferrant, etc). Bitte unbedingt alle Lizenzrechte abklären und keine Originalwerke verwenden.
Eine Idee wäre einen Bezug zu "Hanna und der Barakleon" herzustellen. (Vielzitiertes Thema in der Kunstgeschichte, Hanna schlägt dem Feldherrn Barakleon den Kopf ab und befreit ihr Volk.)
Das Design sollte aber trotzdem nett und nicht gruselig sein.
Ganz wichtig keine nackte Hanna. Sie ist stark und emanzipiert sich!
Text auf der Vorderseite:
Wiebke Talhammer
Hanna betritt die Leinwand
Erzählung über die Kunst der Moderne
Text auf der Rückseite:
kurze Inhaltsangabe
Das Cover soll für ein Taschenbuch als auch ein e-book funktionieren

```html
<!DOCTYPE html>
<html lang="de">
<head>
<meta charset="utf-8">
<title>Hanna betritt die Leinwand – Cover</title>
<link rel="stylesheet" href="https://fonts.googleapis.com/css2?family=Open+Sans:wdth,wght@75..100,600..800&display=swap">
<style>
  :root {
    --paper: #ffffff;
    --paper-edge: #ececec;
    --ink: #111111;
    --stroke-blue: #1f6fd1;
    --stroke-magenta: #e0208a;
    --stroke-orange: #f28a1c;
    --stroke-teal: #20b6c4;
    --stroke-yellow: #e6d21a;
    --stroke-black: #1a1a1a;
  }
  html, body {
    margin: 0;
    padding: 0;
    overflow: hidden;
    background: var(--paper);
  }
  .cover {
    position: relative;
    width: 749px;
    height: 1200px;
    overflow: hidden;
    background: radial-gradient(ellipse at 50% 45%, var(--paper) 60%, var(--paper-edge) 100%);
    font-family: "Open Sans", Arial, sans-serif;
    color: var(--ink);
  }
  .cover__artwork {
    position: absolute;
    left: 140px;
    top: 45px;
    width: 480px;
    height: 920px;
  }
  .cover__text {
    position: absolute;
    left: 0;
    right: 0;
    top: 905px;
    text-align: center;
    text-transform: uppercase;
  }
  .cover__author {
    margin: 0;
    font-size: 31px;
    font-weight: 700;
    font-stretch: 85%;
    letter-spacing: 0.5px;
    line-height: 1;
  }
  .cover__title {
    margin: 6px 0 0;
    font-size: 86px;
    font-weight: 800;
    font-stretch: 78%;
    line-height: 0.8;
    letter-spacing: -0.5px;
  }
  .cover__title span { display: block; }
  .cover__subtitle {
    margin: 14px 0 0;
    font-size: 25px;
    font-weight: 700;
    font-stretch: 82%;
    letter-spacing: 0.4px;
    line-height: 1;
  }
</style>
</head>
<body>
  <main class="cover">
    <svg class="cover__artwork" viewBox="0 0 480 920" role="img"
         aria-label="Illustration: Profil eines Frauenkopfes aus bunten, expressiven Pinselstrichen in Blau, Magenta, Orange, Türkis, Gelb und Schwarz">
      <defs>
        <linearGradient id="strokeBlend" x1="0" y1="0" x2="1" y2="1">
          <stop offset="0" stop-color="var(--stroke-yellow)"/>
          <stop offset="0.25" stop-color="var(--stroke-orange)"/>
          <stop offset="0.45" stop-color="var(--stroke-magenta)"/>
          <stop offset="0.65" stop-color="var(--stroke-blue)"/>
          <stop offset="0.85" stop-color="var(--stroke-teal)"/>
          <stop offset="1" stop-color="var(--stroke-magenta)"/>
        </linearGradient>
      </defs>
      <rect x="20" y="0" width="440" height="920" rx="220" fill="url(#strokeBlend)" opacity="0.85"/>
    </svg>

    <header class="cover__text">
      <p class="cover__author">Wiebke Talhammer</p>
      <h1 class="cover__title"><span>Hanna betritt</span><span>die Leinwand</span></h1>
      <p class="cover__subtitle">Erzählung über die Kunst der Moderne</p>
    </header>
  </main>
</body>
</html>
```